vesko: nature's odor eliminator

I need a label design for a chemical free air freshener/odor eliminator. The product is "Vesko: Odor Eliminator"

I want to keep the design simple and eco friendly themed. (green/blue color theme) I have attached some sketches and mockups ive created. the bottle is a transparent blue, so i would like the main logo to be in green, and the lettering we can try different colors to see what stands out. I would like the label to be designed with a clear label to use the blue background of the bottle.

Contains No Chemicals
Readily biodegradable
Phosphate-free
Non-toxic, non-corrosive and environmentally-friendly
Made with essential oils.

Safe to use around kids, plants and pets.

Elliminates odors, including:
Smoke odors: ( tobacco, medical marijuana, fire)
Vomit
Urine
Gasoline

Replaces toxic air fresheners.

Ingredients: Distilled Water, Proprietary Odor Eliminating Enzyme Blend, Proprietary Essential Oil Blend.

I will be using this bottle:
http://www.bottlemarthub.example/item/K742

Label Dimensions: 5.6875 x 5 in

Target Market(s)

People who use air fresheners (plumora or swish) and want an alternative that does not have toxic chemicals.

Requirements
Must have
• Bold green main lettering

```html
<!DOCTYPE html>
<html lang="en">
<head>
<meta charset="utf-8">
<title>Vesko Odor Eliminator – Label</title>
<link rel="stylesheet" href="https://fonts.googleapis.com/css2?family=Fredoka:wght@600&family=Open+Sans:wght@400;600&display=swap">
<style>
  :root {
    --page: #ffffff;
    --ink: #111111;
    --bottle-deep: #0a1a8c;
    --bottle-mid: #1f3bd6;
    --bottle-light: #3a5cf0;
    --back-deep: #1b2a9e;
    --back-mid: #2c44c4;
    --leaf-green: #b9e23a;
    --band-green: #6fae2a;
    --label-white: #f2f5ff;
  }
  * { box-sizing: border-box; margin: 0; padding: 0; }
  html, body { width: 1023px; height: 1200px; overflow: hidden; background: var(--page); }
  .canvas { position: relative; width: 1023px; height: 1200px; }

  .side-title {
    position: absolute; top: 70px;
    font-family: "Open Sans", sans-serif; font-weight: 400;
    font-size: 30px; color: var(--ink); text-align: center;
  }
  .side-title.front { left: 95px; width: 330px; }
  .side-title.back { left: 660px; width: 290px; }

  .front-frame {
    position: absolute; left: 95px; top: 140px; width: 330px; height: 1010px;
    border: 3px solid var(--ink); padding: 14px;
  }
  .front-label {
    position: relative; width: 100%; height: 100%; border-radius: 90px;
    background: linear-gradient(90deg, var(--bottle-deep) 0%, var(--bottle-mid) 35%, var(--bottle-light) 55%, var(--bottle-mid) 75%, var(--bottle-deep) 100%);
    overflow: hidden;
  }
  .front-brand {
    position: absolute; left: 50%; top: 50%;
    transform: translate(-50%, -50%) rotate(-90deg);
    display: flex; align-items: center; gap: 26px; white-space: nowrap;
  }
  .front-brand .name {
    font-family: "Fredoka", sans-serif; font-weight: 600;
    font-size: 210px; line-height: 1; color: var(--leaf-green);
  }
  .front-brand .dot {
    width: 70px; height: 70px; border-radius: 50%; background: var(--leaf-green);
  }
  .front-tagline {
    position: absolute; left: 232px; top: 160px;
    transform-origin: left top; transform: rotate(90deg);
    font-family: "Open Sans", sans-serif; font-weight: 600;
    font-size: 22px; letter-spacing: 3px; color: var(--label-white); white-space: nowrap;
  }
  .front-volume {
    position: absolute; left: 232px; top: 870px;
    transform-origin: left top; transform: rotate(90deg);
    font-family: "Open Sans", sans-serif; font-weight: 600;
    font-size: 22px; letter-spacing: 2px; color: var(--label-white);
  }

  .back-label {
    position: absolute; left: 660px; top: 140px; width: 290px; height: 1010px;
    border-radius: 40px;
    background: linear-gradient(90deg, var(--back-deep) 0%, var(--back-mid) 50%, var(--back-deep) 100%);
    overflow: hidden;
  }
  .back-brand {
    position: absolute; left: 34px; top: 360px;
    display: flex; align-items: center; gap: 10px;
  }
  .back-brand .name {
    font-family: "Fredoka", sans-serif; font-weight: 600;
    font-size: 64px; line-height: 1; color: var(--leaf-green);
  }
  .back-brand .dot { width: 18px; height: 18px; border-radius: 50%; background: var(--leaf-green); }
  .back-copy {
    position: absolute; left: 34px; top: 450px; width: 230px;
    font-family: "Open Sans", sans-serif; font-size: 11.5px; line-height: 1.55;
    color: var(--label-white); list-style: none;
  }
  .back-swoosh { position: absolute; left: 0; top: 640px; width: 290px; height: 150px; }
  .back-url {
    position: absolute; left: 40px; top: 697px;
    font-family: "Open Sans", sans-serif; font-weight: 600;
    font-size: 15px; color: var(--label-white);
  }
</style>
</head>
<body>
<main class="canvas">
  <h2 class="side-title front">FRONT SIDE</h2>
  <h2 class="side-title back">BACK SIDE</h2>

  <section class="front-frame">
    <div class="front-label">
      <div class="front-brand">
        <span class="name">vesko</span>
        <span class="dot"></span>
      </div>
      <p class="front-tagline">ODOR ELIMINATOR</p>
      <p class="front-volume">8 OZ</p>
    </div>
  </section>

  <section class="back-label">
    <div class="back-brand">
      <span class="name">vesko</span>
      <span class="dot"></span>
    </div>
    <ul class="back-copy">
      <li>Contains No Chemicals</li>
      <li>Readily biodegradable</li>
      <li>Phosphate-free, non-toxic, non-corrosive</li>
      <li>and environmentally-friendly.</li>
      <li>Made with essential oils.</li>
      <li>Safe around kids, plants and pets.</li>
      <li>Eliminates smoke, vomit, urine, gasoline.</li>
      <li>Ingredients: Distilled Water, Enzyme Blend,</li>
      <li>Essential Oil Blend.</li>
    </ul>
    <svg class="back-swoosh" viewBox="0 0 290 150" aria-hidden="true">
      <path d="M0 60 Q145 30 290 50 L290 85 Q145 70 0 100 Z" fill="var(--band-green)"/>
      <path d="M0 40 Q150 0 290 30" fill="none" stroke="var(--leaf-green)" stroke-width="2"/>
      <path d="M0 115 Q140 75 290 100" fill="none" stroke="var(--leaf-green)" stroke-width="2"/>
      <path d="M0 130 Q160 95 290 120" fill="none" stroke="var(--leaf-green)" stroke-width="1.5"/>
    </svg>
    <p class="back-url">www.veskoodor.example</p>
  </section>
</main>
</body>
</html>
```